We need a card and logo design for a new business based in Dallas Texas called Stonemarsh Financial LLC.

We provide bridge loans.We offer pay day loans,title loans and check cashing.Our products are emmergency loans that help borrowers meet short term liquidity needs until the next pay check.

The final design should communicate,professionalism,Sophistication and friendliness to our customers.Use the color Blue as much as possible and another eye catching color if possible.We will consider a profesional looking knight logo with the color Blue in it.Please design a full corporate identity.

```html
<!DOCTYPE html>
<html lang="en">
<head>
<meta charset="utf-8">
<title>Stonemarsh Financial LLC — Business Card</title>
<link href="https://fonts.googleapis.com/css2?family=Cinzel:wght@500&family=Open+Sans:wght@400;600&display=swap" rel="stylesheet">
<style>
  :root {
    --backdrop: #36312e;
    --paper: #f1f2f4;
    --navy: #2a3f7e;
    --ink: #1a1a1a;
    --rule: #8a8a8a;
    --royal-center: #0b55b0;
    --royal-edge: #1f3d80;
    --white: #ffffff;
    --faint-mark: rgba(255, 255, 255, 0.75);
  }
  html, body {
    margin: 0;
    padding: 0;
    width: 1000px;
    height: 1200px;
    overflow: hidden;
    background: var(--backdrop);
  }
  .canvas {
    position: relative;
    width: 1000px;
    height: 1200px;
  }
  .card {
    position: absolute;
    width: 723px;
    height: 423px;
    overflow: hidden;
  }

  /* Front side */
  .card--front {
    left: 140px;
    top: 119px;
    background: var(--paper);
  }
  .holder {
    position: absolute;
    right: 36px;
    top: 44px;
    text-align: right;
  }
  .holder__name {
    font-family: "Cinzel", serif;
    font-weight: 500;
    font-size: 26px;
    color: var(--navy);
    letter-spacing: 0.5px;
    line-height: 30px;
  }
  .holder__title {
    font-family: "Open Sans", sans-serif;
    font-weight: 600;
    font-size: 18px;
    color: var(--ink);
    line-height: 24px;
  }
  .wordmark {
    position: absolute;
    display: flex;
    align-items: center;
    gap: 14px;
    font-family: "Cinzel", serif;
    font-weight: 500;
  }
  .wordmark__dot {
    border-radius: 50%;
    flex: none;
  }
  .wordmark__text {
    text-align: center;
    line-height: 1;
  }
  .wordmark__name { display: block; }
  .wordmark__sub { display: block; }

  .card--front .wordmark {
    left: 162px;
    top: 120px;
    color: var(--navy);
  }
  .card--front .wordmark__dot {
    width: 56px;
    height: 56px;
    background: var(--navy);
  }
  .card--front .wordmark__name { font-size: 40px; letter-spacing: 1px; }
  .card--front .wordmark__sub { font-size: 24px; margin-top: 6px; }

  .watermark-disc {
    position: absolute;
    right: -60px;
    bottom: -80px;
    width: 300px;
    height: 300px;
    border-radius: 50%;
    background: var(--faint-mark);
  }
  .contact {
    position: absolute;
    top: 276px;
    font-family: "Open Sans", sans-serif;
    font-size: 16px;
    line-height: 22px;
    color: var(--ink);
    border-collapse: collapse;
  }
  .contact td { padding: 0 0 9px 0; vertical-align: top; }
  .contact__label {
    color: var(--navy);
    font-weight: 600;
    padding-right: 7px !important;
  }
  .contact--left { left: 51px; }
  .contact--right { left: 393px; }
  .contact--right .contact__label { width: 68px; }
  .contact-divider {
    position: absolute;
    left: 375px;
    top: 269px;
    width: 1px;
    height: 80px;
    background: var(--rule);
  }

  /* Back side */
  .card--back {
    left: 125px;
    top: 638px;
    background: radial-gradient(ellipse 60% 65% at 50% 40%, var(--royal-center) 0%, var(--royal-edge) 100%);
  }
  .card--back .wordmark {
    left: 0;
    right: 0;
    top: 90px;
    flex-direction: column;
    gap: 30px;
    color: var(--white);
  }
  .card--back .wordmark__dot {
    width: 120px;
    height: 120px;
    background: var(--white);
  }
  .card--back .wordmark__name { font-size: 44px; letter-spacing: 1px; }
  .card--back .wordmark__sub { font-size: 27px; margin-top: 8px; }
</style>
</head>
<body>
<main class="canvas">

  <section class="card card--front" aria-label="Business card front">
    <div class="watermark-disc" aria-hidden="true"></div>

    <div class="holder">
      <div class="holder__name">DANIEL REYES</div>
      <div class="holder__title">Financial Advisor</div>
    </div>

    <div class="wordmark">
      <span class="wordmark__dot" aria-hidden="true"></span>
      <span class="wordmark__text">
        <span class="wordmark__name">STONEMARSH</span>
        <span class="wordmark__sub">FINANCIAL LLC.</span>
      </span>
    </div>

    <table class="contact contact--left">
      <tr><td class="contact__label">Phone:</td><td>111-123-4567</td></tr>
      <tr><td class="contact__label">Email:</td><td>info@stonemarshfinancial.com</td></tr>
    </table>

    <div class="contact-divider" aria-hidden="true"></div>

    <table class="contact contact--right">
      <tr><td class="contact__label">Fax:</td><td>111-123-4567</td></tr>
      <tr><td class="contact__label">Address:</td><td>XXX Some Street Address<br>State, Country</td></tr>
    </table>
  </section>

  <section class="card card--back" aria-label="Business card back">
    <div class="wordmark">
      <span class="wordmark__dot" aria-hidden="true"></span>
      <span class="wordmark__text">
        <span class="wordmark__name">STONEMARSH</span>
        <span class="wordmark__sub">FINANCIAL LLC.</span>
      </span>
    </div>
  </section>

</main>
</body>
</html>
```